BrivoTerna. Lantern of the Steady Harvest. Business card

Professional business card for BrivoTerna (Lantern of the Steady Harvest)
My rationale: Strategy-> Execution-> Results-> Value that lead to the BrivoTerna name: We put the Lantern of the Steady Harvest.
We deliver value to our customers helping them at defining a good strategy (cyan arrow). 90% of well formulated strategies fail due to poor execution so we also consider strategical execution very important (green arrow). Due to the execution we obtain the results (blue arrow). Finally, the results provide feedback to redefine strategy, and the new strategy has to be executed and new results obtained providing new feedback and on and on. It's like a wheel that finally, must create corporate value: value for shareholders, staholders, employees, providers...-

Target Market(s)

CEOs and steering comitees , invewrnent funds

Industry/Entity Type

Business Consultant

Contact Information for Business Card

Teodoro Vinsquel
CEO & Founder
teodoro.vinsquel@brivoterna-example.com
Mobile: +34 655.803.912
www.brivoterna-example.com

Colors

Designer to choose colors to be used in the design.

Requirements
Nice to have
• Nice to hace the words: Strategy, execution, results
• Nice to vave the claim: Lantern of the Steady Harvest
• The three colors should be shown:
• cyan for STRATEGY
• green for EXECUTION
• blue for RESULTS
Should not have
• Complete black background

```html
<!DOCTYPE html>
<html lang="en">
<head>
<meta charset="utf-8">
<title>BrivoTerna – Business Card</title>
<link rel="stylesheet" href="https://fonts.googleapis.com/css2?family=PT+Sans:wght@400;700&display=swap">
<style>
  :root {
    --royal-blue: #0a3596;
    --strategy-cyan: #1aa8e6;
    --execution-green: #8cc63f;
    --card-white: #ffffff;
    --backdrop: #e4e6ea;
    --text-light: #ffffff;
  }
  * { margin: 0; padding: 0; box-sizing: border-box; }
  html, body {
    width: 1200px; height: 900px; overflow: hidden;
    background: var(--backdrop);
    font-family: "PT Sans", sans-serif;
  }
  .canvas { position: relative; width: 1200px; height: 900px; }

  .card {
    position: absolute;
    width: 620px; height: 354px;
    border-radius: 18px;
    overflow: hidden;
    background: var(--card-white);
    box-shadow: 0 14px 30px rgba(20, 30, 60, 0.18);
  }
  .card-front { left: 110px; top: 80px; }
  .card-back  { left: 470px; top: 466px; }

  .front-art { position: absolute; inset: 0; width: 620px; height: 354px; }

  .front-wordmark {
    position: absolute; left: 30px; top: 196px;
    font-weight: 700; font-size: 38px; letter-spacing: -0.8px;
    color: var(--royal-blue);
    display: flex; align-items: center; gap: 10px;
  }
  .wordmark-dot {
    width: 12px; height: 12px; border-radius: 50%;
    background: var(--royal-blue);
  }

  .contact-block {
    position: absolute; right: 28px; top: 28px;
    text-align: right; color: var(--text-light);
  }
  .person-name { font-weight: 700; font-size: 20px; line-height: 1.1; }
  .person-title { font-size: 13px; margin-bottom: 38px; }
  .contact-line {
    display: flex; justify-content: flex-end; align-items: center; gap: 7px;
    font-size: 12px; line-height: 21px;
  }
  .contact-line svg { width: 12px; height: 12px; flex: none; }

  .tagline {
    position: absolute; right: 28px; bottom: 26px;
    font-weight: 700; font-size: 15px; color: var(--execution-green);
  }
  .tagline .sep { color: var(--strategy-cyan); margin: 0 5px; }

  .back-wordmark {
    position: absolute; left: 0; right: 0; top: 138px;
    text-align: center;
    font-weight: 700; font-size: 72px; letter-spacing: -1.5px;
    color: var(--royal-blue);
  }
</style>
</head>
<body>
<main class="canvas">

  <section class="card card-front" aria-label="Business card front">
    <svg class="front-art" viewBox="0 0 620 354" aria-hidden="true">
      <rect width="620" height="354" fill="var(--royal-blue)"/>
      <circle cx="-260" cy="300" r="576" fill="var(--execution-green)"/>
      <circle cx="-260" cy="300" r="564" fill="var(--strategy-cyan)"/>
      <circle cx="-260" cy="300" r="552" fill="var(--card-white)"/>
    </svg>

    <div class="front-wordmark">BrivoTerna<span class="wordmark-dot"></span></div>

    <div class="contact-block">
      <p class="person-name">Teodoro Vinsquel</p>
      <p class="person-title">CEO &amp; Founder</p>
      <p class="contact-line">+34 655.803.912
        <svg viewBox="0 0 14 14" fill="none" stroke="var(--strategy-cyan)" stroke-width="1.4"><rect x="3.5" y="1" width="7" height="12" rx="1.2"/><line x1="6" y1="11" x2="8" y2="11"/></svg>
      </p>
      <p class="contact-line">teodoro.vinsquel@brivoterna-example.com
        <svg viewBox="0 0 14 14" fill="none" stroke="var(--strategy-cyan)" stroke-width="1.4"><rect x="1" y="3" width="12" height="8" rx="1"/><polyline points="1,3 7,8 13,3"/></svg>
      </p>
      <p class="contact-line">www.brivoterna-example.com
        <svg viewBox="0 0 14 14" fill="none" stroke="var(--strategy-cyan)" stroke-width="1.3"><circle cx="7" cy="7" r="6"/><ellipse cx="7" cy="7" rx="2.6" ry="6"/><line x1="1" y1="7" x2="13" y2="7"/></svg>
      </p>
    </div>

    <p class="tagline">Results<span class="sep">•</span>Execution<span class="sep">•</span>Strategy</p>
  </section>

  <section class="card card-back" aria-label="Business card back">
    <p class="back-wordmark">BrivoTerna</p>
  </section>

</main>
</body>
</html>
```